Kestova Information Posters for Student signage

Secondary school looking for some posters to display throughout the school with fresh designs using school colours and fitting with general feel of the school's graphic image. The final designs should be welcoming but clearly outline the required instructions. Sample designs that have been created by the school are attached with the relevant information that is required to appear on the signs. School would like a more dynamic design than the basic signs attached.
We are looking for:
- Large pop-up banner style size for the 2 posters called
"Ready for class" and "Morning Routine".
- Printable poster for the "Kestova Outdoor" sign.

Please incorporate a design feature of "the Kestova 1,2,3" into the posters and also use the Kestova Leaner values of Integrity, Compassion, Curiosity and Drive to help illustrate the content.

An option for design is to incorporate our school's first nations artwork into the design and i have also provided various extracts of design pieces that the school often uses in it's marketing materials.

Target Market(s)

Secondary School Students

Industry/Entity Type

Education

Colors
00AB8E
00BBA5
67D7C9
C6EFE9
E9F9F6
FFF300
FFF600
FEFA6F
FFFEC7
FFFEE8
FFC000
F8CF3A
FAE287
FDF2CF
FEFAEE

Requirements
Must have
• My project must have eyecatching graphics

```html
<!DOCTYPE html>
<html lang="en">
<head>
<meta charset="utf-8">
<title>Kestova – Ready for Class</title>
<link rel="stylesheet" href="https://fonts.googleapis.com/css2?family=Poppins:wght@400;700;800&display=swap">
<style>
  :root {
    --green-deep: #1b3f20;
    --green-soft: #5f7d62;
    --yellow: #f6d10f;
    --paper: #f7f7f4;
    --white: #ffffff;
    --rule: #b9b9b0;
  }
  * { margin: 0; padding: 0; box-sizing: border-box; }
  html, body { width: 800px; height: 1200px; overflow: hidden; background: var(--paper); }
  body { font-family: "Poppins", sans-serif; color: var(--green-deep); }

  .banner { position: relative; width: 800px; height: 1200px; background: var(--paper); overflow: hidden; }
  .banner-waves { position: absolute; inset: 0; width: 800px; height: 1200px; }

  .headline {
    position: absolute; top: 215px; left: 0; width: 800px;
    text-align: center; font-weight: 800; font-size: 78px; line-height: 86px;
    letter-spacing: -1px;
  }

  .steps-tab {
    position: absolute; top: 410px; left: 190px; width: 420px; height: 112px;
    border: 5px solid var(--yellow); border-radius: 22px; background: var(--white);
    overflow: hidden; z-index: 2;
  }
  .steps-tab__title { height: 52px; line-height: 54px; text-align: center; font-weight: 800; font-size: 38px; }
  .steps-tab__numbers {
    height: 55px; background: var(--yellow);
    display: flex; justify-content: space-around; align-items: center; padding: 0 40px;
  }
  .step-number {
    width: 42px; height: 42px; border-radius: 50%; background: var(--green-deep);
    color: var(--white); font-weight: 700; font-size: 24px; line-height: 43px; text-align: center;
  }

  .checklist {
    position: absolute; top: 470px; left: 90px; width: 620px; height: 500px;
    border: 4px solid var(--yellow); border-radius: 30px; background: var(--white);
    padding: 62px 40px 0 40px;
  }
  .checklist-item { display: flex; align-items: center; gap: 32px; height: 118px; }
  .checklist-item + .checklist-item { border-top: 2px dotted var(--rule); margin-top: 10px; padding-top: 10px; height: 140px; }
  .checklist-item__icon {
    flex: 0 0 112px; width: 112px; height: 112px; border-radius: 50%; background: var(--yellow);
    display: flex; align-items: center; justify-content: center;
  }
  .checklist-item__label { font-weight: 800; font-size: 44px; line-height: 46px; letter-spacing: -0.5px; }
  .checklist-item__note { display: block; font-weight: 700; font-size: 28px; line-height: 36px; letter-spacing: 0; }

  .values-footer { position: absolute; left: 200px; width: 400px; top: 1100px; text-align: center; }
  .values-footer__title { color: var(--white); font-weight: 700; font-size: 30px; line-height: 38px; }
  .values-footer__subtitle { color: var(--yellow); font-weight: 400; font-size: 22px; line-height: 30px; }

  .school-mark { position: absolute; right: 30px; top: 1108px; display: flex; align-items: center; gap: 10px; }
  .school-mark__dot { width: 36px; height: 36px; border-radius: 50%; background: var(--yellow); }
  .school-mark__name { color: var(--yellow); font-weight: 800; font-size: 28px; line-height: 36px; }
</style>
</head>
<body>
<main class="banner">
  <svg class="banner-waves" viewBox="0 0 800 1200" role="img" aria-label="Flowing First Nations style wave bands in school yellow and green">
    <path d="M0 0 H800 V60 C660 20 560 110 420 140 C290 170 150 130 0 190 Z" fill="#f6d10f"/>
    <path d="M0 160 C150 110 280 150 420 118 C560 88 660 10 800 40" fill="none" stroke="#ffffff" stroke-width="8"/>
    <path d="M0 1015 C160 975 270 1045 430 1035 C590 1022 690 955 800 945 V1200 H0 Z" fill="#1b3f20"/>
    <path d="M0 1050 C160 1010 280 1070 440 1060 C600 1048 700 985 800 975" fill="none" stroke="#5f7d62" stroke-width="10"/>
  </svg>

  <h1 class="headline">Are you ready<br>for class?</h1>

  <div class="steps-tab">
    <div class="steps-tab__title">The Kestova</div>
    <div class="steps-tab__numbers">
      <span class="step-number">1</span>
      <span class="step-number">2</span>
      <span class="step-number">3</span>
    </div>
  </div>

  <section class="checklist">
    <div class="checklist-item">
      <div class="checklist-item__icon">
        <svg width="74" height="56" viewBox="0 0 74 56" aria-hidden="true">
          <rect x="10" y="2" width="54" height="40" rx="4" fill="#1b3f20"/>
          <rect x="2" y="44" width="70" height="8" rx="3" fill="#1b3f20"/>
          <rect x="30" y="44" width="14" height="3" fill="#f6d10f"/>
        </svg>
      </div>
      <div class="checklist-item__label">Laptop /<br>workbook</div>
    </div>
    <div class="checklist-item">
      <div class="checklist-item__icon">
        <svg width="50" height="80" viewBox="0 0 50 80" aria-hidden="true">
          <rect x="4" y="3" width="42" height="74" rx="12" fill="#ffffff" stroke="#1b3f20" stroke-width="4"/>
          <rect x="10" y="16" width="30" height="54" rx="6" fill="#1b3f20"/>
          <circle cx="25" cy="11" r="4" fill="none" stroke="#1b3f20" stroke-width="3"/>
        </svg>
      </div>
      <div class="checklist-item__label">Phone in<br>Pocketa</div>
    </div>
    <div class="checklist-item">
      <div class="checklist-item__icon">
        <svg width="84" height="50" viewBox="0 0 84 50" aria-hidden="true">
          <path d="M22 8 Q42 0 62 8 L66 34 H18 Z" fill="#1b3f20"/>
          <rect x="19" y="26" width="46" height="5" fill="#f6d10f"/>
          <ellipse cx="42" cy="38" rx="40" ry="9" fill="#1b3f20"/>
        </svg>
      </div>
      <div class="checklist-item__label">Correct<br>uniform<span class="checklist-item__note">(Including hat)</span></div>
    </div>
  </section>

  <footer>
    <div class="values-footer">
      <p class="values-footer__title">Curiosity and Drive</p>
      <p class="values-footer__subtitle">Kestova Learner Values</p>
    </div>
    <div class="school-mark">
      <span class="school-mark__dot"></span>
      <span class="school-mark__name">Kestova</span>
    </div>
  </footer>
</main>
</body>
</html>
```